TAVILN soap beauty bar

I need a box designed to put a 4oz bar of soap inside. All sides of the box need design. A refreshingly fragrant blend of citrus and spicy notes, it is made with a blend of essential oils including ginger, mandarin, lemon and orange flowers

Target Market(s)

Homeless people

Requirements
Must have
• My company logo as pictured with text and design like a standard bar of soap. Weight 4oz, ingredients:
Olive oil, Coconut oil,Organic sustainable palm oil,Water,Lye,Shea butter, orange, ginger, mandarin, lemon essential oil. uploading pics for inspiration.
Nice to have
• The soap box measurements are Dimensions (L x W x H). 5.75 x 3.80 x 5.60 Inches ...

```html
<!DOCTYPE html>
<html lang="en">
<head>
<meta charset="utf-8">
<title>TAVILN Soap Beauty Bar – Box Dieline</title>
<link rel="stylesheet" href="https://fonts.googleapis.com/css2?family=Righteous&family=Poiret+One&family=Comfortaa:wght@400&display=swap">
<style>
  :root {
    --plum-dark: #2c0a2c;
    --plum-mid: #4a0f48;
    --plum-light: #741a6e;
    --gold: #ecd21e;
    --leaf-green: #46a82a;
    --cut-red: #e3222b;
    --paper: #ffffff;
    --label-white: #ffffff;
  }
  html, body {
    margin: 0;
    padding: 0;
    width: 961px;
    height: 1200px;
    overflow: hidden;
    background: var(--paper);
  }
  .canvas {
    position: relative;
    width: 961px;
    height: 1200px;
  }
  .dieline {
    position: absolute;
    left: 0;
    top: 270px;
    width: 961px;
    height: 660px;
  }
  .print-flap, .print-panel { stroke: var(--cut-red); stroke-width: 1.2; }
  .blank-flap { fill: var(--paper); stroke: var(--cut-red); stroke-width: 1.4; }
  .title { font-family: 'Righteous', sans-serif; fill: var(--gold); }
  .subtitle { font-family: 'Poiret One', sans-serif; fill: var(--gold); }
  .brand { font-family: 'Righteous', sans-serif; fill: var(--leaf-green); }
  .body-copy { font-family: 'Comfortaa', sans-serif; fill: var(--paper); font-size: 13px; }
  .body-copy--gold { fill: var(--gold); font-size: 13px; }
  .gold-rule { fill: var(--gold); }
  .copy-frame { fill: none; stroke: var(--paper); stroke-width: 2; }
  .flower-art { fill: var(--gold); fill-opacity: 0.1; }
  .brand-dot { fill: #d8141b; }
  .label-tag { fill: var(--label-white); }
</style>
</head>
<body>
<main class="canvas">
<svg class="dieline" viewBox="25 985 1675 1150" xmlns="http://www.w3.org/2000/svg">
  <defs>
    <linearGradient id="panelShade" x1="0" y1="0" x2="1" y2="0">
      <stop offset="0" stop-color="var(--plum-dark)"/>
      <stop offset="0.55" stop-color="var(--plum-mid)"/>
      <stop offset="1" stop-color="var(--plum-light)"/>
    </linearGradient>
    <linearGradient id="flapShadeUp" x1="0" y1="0" x2="0" y2="1">
      <stop offset="0" stop-color="var(--plum-dark)"/>
      <stop offset="1" stop-color="var(--plum-light)"/>
    </linearGradient>
    <linearGradient id="flapShadeDown" x1="0" y1="1" x2="0" y2="0">
      <stop offset="0" stop-color="var(--plum-dark)"/>
      <stop offset="1" stop-color="var(--plum-light)"/>
    </linearGradient>
  </defs>

  <!-- Blank glue and dust flaps -->
  <polygon class="blank-flap" points="830,1310 880,1095 1108,1095 1158,1260 1158,1310"/>
  <polygon class="blank-flap" points="830,1805 880,2020 1108,2020 1158,1855 1158,1805"/>
  <polygon class="blank-flap" points="1158,1310 1175,1215 1220,1200 1262,1140 1262,1040 1533,1040 1533,1140 1575,1200 1620,1215 1638,1310"/>
  <polygon class="blank-flap" points="1158,1805 1175,1900 1220,1915 1262,1975 1262,2075 1533,2075 1533,1975 1575,1915 1620,1900 1638,1805"/>
  <polygon class="blank-flap" points="1638,1310 1695,1355 1695,1765 1638,1805"/>

  <!-- Printed side flaps -->
  <polygon class="print-flap" fill="url(#flapShadeUp)" points="25,1310 25,1260 80,1090 295,1090 352,1310"/>
  <polygon class="print-flap" fill="url(#flapShadeDown)" points="25,1805 25,1855 80,2025 295,2025 352,1805"/>

  <!-- Top lid -->
  <g class="lid lid--top">
    <polygon class="print-flap" fill="url(#flapShadeUp)" points="352,1310 366,1260 366,985 818,985 818,1260 830,1310"/>
    <circle class="brand-dot" cx="592" cy="1078" r="30"/>
    <text class="brand" x="592" y="1172" font-size="44" text-anchor="middle">TAVILN</text>
    <text class="title" x="592" y="1213" font-size="30" text-anchor="middle" letter-spacing="1">TAVILN SOAP</text>
    <text class="subtitle" x="592" y="1296" font-size="36" text-anchor="middle">BEAUTY BAR</text>
  </g>

  <!-- Bottom lid -->
  <g class="lid lid--bottom">
    <polygon class="print-flap" fill="url(#flapShadeDown)" points="352,1805 366,1855 366,2130 818,2130 818,1855 830,1805"/>
    <g transform="rotate(180 592 1557.5)">
      <circle class="brand-dot" cx="592" cy="1078" r="30"/>
      <text class="brand" x="592" y="1172" font-size="44" text-anchor="middle">TAVILN</text>
      <text class="title" x="592" y="1213" font-size="30" text-anchor="middle" letter-spacing="1">TAVILN SOAP</text>
      <text class="subtitle" x="592" y="1296" font-size="36" text-anchor="middle">BEAUTY BAR</text>
    </g>
  </g>

  <!-- Side panel: description -->
  <g class="panel panel--side-left">
    <rect class="print-panel" x="25" y="1310" width="327" height="495" fill="url(#panelShade)"/>
    <rect class="copy-frame" x="70" y="1330" width="238" height="282"/>
    <g class="body-copy">
      <text transform="translate(276,1350) rotate(90)" textLength="218" lengthAdjust="spacingAndGlyphs">Lorem ipsum dolor sit amet, con-</text>
      <text transform="translate(256,1350) rotate(90)" textLength="238" lengthAdjust="spacingAndGlyphs">sectetuer adipiscing elit, sed diam</text>
      <text transform="translate(236,1350) rotate(90)" textLength="204" lengthAdjust="spacingAndGlyphs">nonummy nibh euismod tincidunt</text>
      <text transform="translate(216,1350) rotate(90)" textLength="211" lengthAdjust="spacingAndGlyphs">ut laoreet dolore magna aliquam</text>
      <text transform="translate(196,1350) rotate(90)" textLength="204" lengthAdjust="spacingAndGlyphs">erat volutpat. Ut wisi enim ad</text>
      <text transform="translate(176,1350) rotate(90)" textLength="224" lengthAdjust="spacingAndGlyphs">minim veniam, quis nostrud exerci</text>
      <text transform="translate(156,1350) rotate(90)" textLength="242" lengthAdjust="spacingAndGlyphs">tation ullamcorper suscipit lobortis</text>
      <text transform="translate(136,1350) rotate(90)" textLength="197" lengthAdjust="spacingAndGlyphs">nisl ut aliquip ex ea commodo</text>
      <text transform="translate(116,1350) rotate(90)" textLength="197" lengthAdjust="spacingAndGlyphs">consequat. Duis autem vel eum</text>
      <text transform="translate(96,1350) rotate(90)" textLength="242" lengthAdjust="spacingAndGlyphs">iriure dolor in hendrerit in vulputate</text>
    </g>
    <g role="img" aria-label="Gold line-art flower illustration">
      <ellipse class="flower-art" cx="185" cy="1700" rx="80" ry="75"/>
    </g>
  </g>

  <!-- Front panel -->
  <g class="panel panel--front">
    <rect class="print-panel" x="352" y="1310" width="478" height="495" fill="url(#panelShade)"/>
    <g role="img" aria-label="Gold line-art flower illustration">
      <ellipse class="flower-art" cx="485" cy="1430" rx="85" ry="80"/>
    </g>
    <g role="img" aria-label="Small gold line-art flower illustration">
      <ellipse class="flower-art" cx="762" cy="1395" rx="55" ry="50"/>
    </g>
    <g class="body-copy body-copy--gold">
      <text transform="translate(506,1597) rotate(90)">Lorem ipsum dolor sit</text>
      <text transform="translate(486,1597) rotate(90)">amet, consectetuer</text>
      <text transform="translate(466,1597) rotate(90)" textLength="185" lengthAdjust="spacingAndGlyphs">adipiscing elit, sed diam</text>
      <text transform="translate(446,1597) rotate(90)">nonummy nibh euismod</text>
      <text transform="translate(426,1597) rotate(90)">tincidunt ut laoreet</text>
      <text transform="translate(406,1597) rotate(90)">dolore</text>
    </g>
    <rect class="gold-rule" x="621" y="1312" width="4" height="390"/>
    <text class="title" transform="translate(672,1410) rotate(90)" font-size="40" letter-spacing="1">TAVILN SOAP</text>
    <text class="subtitle" transform="translate(634,1495) rotate(90)" font-size="36">BEAUTY BAR</text>
    <rect class="label-tag" x="743" y="1665" width="65" height="140"/>
    <text class="brand" transform="translate(750,1676) rotate(90)" font-size="14">TAVILN</text>
  </g>

  <!-- Side panel: copy -->
  <g class="panel panel--side-right">
    <rect class="print-panel" x="830" y="1310" width="328" height="495" fill="url(#panelShade)"/>
    <g role="img" aria-label="Gold line-art flower illustration">
      <ellipse class="flower-art" cx="912" cy="1392" rx="68" ry="64"/>
    </g>
    <g class="body-copy">
      <text transform="translate(1112,1355) rotate(90)" textLength="425" lengthAdjust="spacingAndGlyphs">Lorem ipsum dolor sit amet, consectetuer adipiscing elit, sed</text>
      <text transform="translate(1092,1355) rotate(90)" textLength="425" lengthAdjust="spacingAndGlyphs">diam nonummy nibh euismod tincidunt ut laoreet dolore</text>
      <text transform="translate(1072,1355) rotate(90)" textLength="425" lengthAdjust="spacingAndGlyphs">magna aliquam erat volutpat. Ut wisi enim ad minim veniam,</text>
      <text transform="translate(1052,1355) rotate(90)" textLength="425" lengthAdjust="spacingAndGlyphs">quis nostrud exerci tation ullamcorper suscipit lobortis nisl ut</text>
      <text transform="translate(1032,1355) rotate(90)" textLength="425" lengthAdjust="spacingAndGlyphs">aliquip ex ea commodo consequat. Duis autem vel eum iriure</text>
      <text transform="translate(934,1525) rotate(90)">Lorem ipsum dolor sit amet,</text>
      <text transform="translate(914,1525) rotate(90)" textLength="225" lengthAdjust="spacingAndGlyphs">consectetuer adipiscing elit, sed</text>
      <text transform="translate(894,1525) rotate(90)">diam nonummy nibh euismod</text>
      <text transform="translate(874,1525) rotate(90)">tincidunt ut laoreet dolore</text>
    </g>
  </g>

  <!-- Back panel -->
  <g class="panel panel--back">
    <rect class="print-panel" x="1158" y="1310" width="480" height="495" fill="url(#panelShade)"/>
    <g role="img" aria-label="Gold line-art flower illustration">
      <ellipse class="flower-art" cx="1288" cy="1435" rx="85" ry="80"/>
    </g>
    <g role="img" aria-label="Small gold line-art flower illustration">
      <ellipse class="flower-art" cx="1568" cy="1398" rx="55" ry="50"/>
    </g>
    <g class="body-copy body-copy--gold">
      <text transform="translate(1312,1600) rotate(90)">Lorem ipsum dolor sit</text>
      <text transform="translate(1292,1600) rotate(90)">amet, consectetuer</text>
      <text transform="translate(1272,1600) rotate(90)" textLength="185" lengthAdjust="spacingAndGlyphs">adipiscing elit, sed diam</text>
      <text transform="translate(1252,1600) rotate(90)">nonummy nibh euismod</text>
      <text transform="translate(1232,1600) rotate(90)">tincidunt ut laoreet</text>
      <text transform="translate(1212,1600) rotate(90)">dolore</text>
    </g>
    <rect class="gold-rule" x="1427" y="1312" width="4" height="392"/>
    <text class="title" transform="translate(1477,1412) rotate(90)" font-size="40" letter-spacing="1">TAVILN SOAP</text>
    <text class="subtitle" transform="translate(1440,1497) rotate(90)" font-size="36">BEAUTY BAR</text>
    <rect class="label-tag" x="1548" y="1668" width="65" height="137"/>
    <text class="brand" transform="translate(1555,1679) rotate(90)" font-size="14">TAVILN</text>
  </g>
</svg>
</main>
</body>
</html>
```